Business card design needed

I would like a one sided black business card with the information provided above. Refer to my website www.brightvolleyracquets.com.au for an example of colors I have used for my site, would like to keep this consistent for my business cards also, I will upload my logo below.

I am a new small business that provides tennis customers with racquet re stringing, tennis strings and accessories.

Industry/Entity Type

Small Business

Contact Information for Business Card

Bright Volley Tennis

Owen Whitby
Managing Director

brightvolleyracquets@mailbox.example
www.brightvolleyracquets.com.au
0491 726 305

Racquet Restringing/Tennis Strings/Accessories

Requirements
Must have
• Must have my logo and card must be black

```html
<!DOCTYPE html>
<html lang="en">
<head>
<meta charset="utf-8">
<title>Bright Volley Tennis – Business Card</title>
<link href="https://fonts.googleapis.com/css2?family=Roboto:wght@300;400;700&display=swap" rel="stylesheet">
<style>
  :root {
    --backdrop: #8b5a35;
    --card-black: #000000;
    --band-top: #6a6a6a;
    --band-mid: #3a3a3a;
    --band-bottom: #1c1c1c;
    --lime: #c5d82e;
    --white: #ffffff;
    --soft-white: #e8e8e8;
    --divider: #9a9a9a;
  }
  * { box-sizing: border-box; margin: 0; padding: 0; }
  html, body {
    width: 1200px;
    height: 475px;
    overflow: hidden;
    background: var(--backdrop);
    font-family: "Roboto", Arial, sans-serif;
  }
  .canvas {
    position: relative;
    width: 1200px;
    height: 475px;
  }
  .card {
    position: absolute;
    background: var(--card-black);
    border-radius: 14px;
    overflow: hidden;
  }
  .card--front { left: 40px; top: 81px; width: 547px; height: 313px; }
  .card--back  { left: 607px; top: 85px; width: 545px; height: 311px; }

  .brand {
    position: absolute;
    left: 0; right: 0;
    display: flex;
    align-items: center;
    justify-content: center;
    gap: 12px;
  }
  .card--front .brand { top: 82px; }
  .card--back .brand  { top: 108px; }
  .brand__dot {
    width: 26px; height: 26px;
    border-radius: 50%;
    background: var(--lime);
  }
  .brand__name {
    color: var(--lime);
    font-weight: 700;
    font-size: 34px;
    letter-spacing: 1px;
    text-transform: uppercase;
  }

  .contact-band {
    position: absolute;
    left: 0; right: 0; bottom: 0;
    height: 118px;
    background: linear-gradient(to bottom, var(--band-top) 0%, var(--band-mid) 45%, var(--band-bottom) 100%);
  }
  .contact-band::before {
    content: "";
    position: absolute;
    top: 0; left: 8%; right: 8%;
    height: 2px;
    background: linear-gradient(to right, transparent, var(--white), transparent);
    opacity: .8;
  }
  .person {
    position: absolute;
    top: 30px; left: 0; right: 0;
    text-align: center;
    white-space: nowrap;
  }
  .person__name {
    color: var(--lime);
    font-size: 17px;
    font-weight: 400;
    letter-spacing: .5px;
    text-transform: uppercase;
  }
  .person__role {
    color: var(--white);
    font-size: 14px;
    font-weight: 400;
    margin-left: 4px;
  }
  .contacts {
    position: absolute;
    top: 72px; left: 0; right: 0;
    display: flex;
    justify-content: center;
    align-items: center;
    color: var(--white);
    font-size: 12px;
    font-weight: 400;
    white-space: nowrap;
  }
  .contacts__item + .contacts__item {
    border-left: 1px solid var(--divider);
    margin-left: 8px;
    padding-left: 8px;
  }

  .web-address {
    position: absolute;
    left: 0; right: 0; top: 240px;
    text-align: center;
    color: var(--soft-white);
    font-size: 13px;
    font-weight: 300;
    letter-spacing: 2px;
  }
</style>
</head>
<body>
<main class="canvas">
  <section class="card card--front" aria-label="Business card front">
    <div class="brand">
      <span class="brand__dot"></span>
      <span class="brand__name">Bright Volley Tennis</span>
    </div>
    <div class="contact-band">
      <p class="person">
        <span class="person__name">Owen Whitby,</span>
        <span class="person__role">Managing Director</span>
      </p>
      <p class="contacts">
        <span class="contacts__item">0491 726 305</span>
        <span class="contacts__item">brightvolleyracquets@mailbox.example</span>
        <span class="contacts__item">www.brightvolleyracquets.com.au</span>
      </p>
    </div>
  </section>

  <section class="card card--back" aria-label="Business card back">
    <div class="brand">
      <span class="brand__dot"></span>
      <span class="brand__name">Bright Volley Tennis</span>
    </div>
    <p class="web-address">www.brightvolleyracquets.com.au</p>
  </section>
</main>
</body>
</html>
```